I'm looking for a smart new design for business cards

Industry/Entity Type

Commercial Electrical

Contact Information for Business Card

Logo, name, email, position, website QR

Requirements
Nice to have
• Logo embedded behind the text side

```html
<!DOCTYPE html>
<html lang="en">
<head>
<meta charset="utf-8">
<title>Brightline Electrical Group — Business Card</title>
<link rel="stylesheet" href="https://fonts.googleapis.com/css2?family=Montserrat:wght@400;500;700;800&display=swap">
<style>
  :root {
    --navy: #262a7a;
    --red: #e31b23;
    --ink: #1c1c1c;
    --paper: #ffffff;
    --card-black: #151515;
    --mark-grey: #3a3a3a;
    --stage: #e9e7e4;
    --edge: #c8141c;
  }
  * { box-sizing: border-box; margin: 0; padding: 0; }
  html, body {
    width: 1200px; height: 919px; overflow: hidden;
    background: var(--stage);
    font-family: "Montserrat", Arial, sans-serif;
  }
  .sheet {
    position: relative; width: 1200px; height: 919px;
    display: flex; align-items: center; justify-content: center; gap: 40px;
  }
  .card {
    position: relative; width: 540px; height: 309px;
    border-radius: 26px;
    box-shadow: 0 4px 0 var(--edge), 0 18px 30px rgba(0,0,0,0.18);
    overflow: hidden;
  }
  .card--front { background: var(--paper); }
  .card--back { background: var(--card-black); }

  /* front: brand block */
  .brand {
    position: absolute; left: 34px; top: 0; bottom: 0; width: 220px;
    display: flex; align-items: center; gap: 12px;
  }
  .brand__square { width: 26px; height: 26px; background: var(--navy); flex: none; }
  .brand__name {
    font-weight: 800; font-size: 21px; line-height: 1.15;
    color: var(--navy); letter-spacing: 0.5px; text-transform: uppercase;
  }
  .divider {
    position: absolute; left: 272px; top: 64px; width: 2px; height: 181px;
    background: var(--red);
  }
  .contact { position: absolute; left: 300px; top: 70px; }
  .contact__name { font-weight: 800; font-size: 28px; line-height: 1.05; letter-spacing: -0.3px; }
  .contact__first { color: var(--navy); }
  .contact__last { color: var(--red); }
  .contact__role { font-weight: 500; font-size: 13px; color: var(--ink); margin-top: 6px; letter-spacing: 0.3px; }
  .contact__list { list-style: none; margin-top: 22px; }
  .contact__item {
    display: flex; align-items: center; gap: 9px;
    font-size: 13px; font-weight: 400; color: var(--ink); margin-bottom: 7px;
  }
  .contact__icon { width: 13px; height: 13px; flex: none; fill: var(--red); }

  /* back: centred brand */
  .back-brand {
    position: absolute; inset: 0;
    display: flex; align-items: center; justify-content: center; gap: 16px;
  }
  .back-brand__square { width: 34px; height: 34px; background: var(--mark-grey); }
  .back-brand__name {
    font-weight: 800; font-size: 27px; line-height: 1.15;
    color: var(--mark-grey); text-transform: uppercase; letter-spacing: 0.6px;
  }
</style>
</head>
<body>
<main class="sheet">
  <section class="card card--front" aria-label="Business card front">
    <div class="brand">
      <span class="brand__square"></span>
      <span class="brand__name">Brightline<br>Electrical<br>Group</span>
    </div>
    <div class="divider"></div>
    <div class="contact">
      <p class="contact__name"><span class="contact__first">Daniel</span> <span class="contact__last">Hartley</span></p>
      <p class="contact__role">Managing Director</p>
      <ul class="contact__list">
        <li class="contact__item">
          <svg class="contact__icon" viewBox="0 0 16 16" aria-hidden="true"><path d="M3.6 1.2l2.3 2.6-1.3 1.9c.9 2 2.5 3.6 4.6 4.6l1.9-1.3 2.6 2.3-1.4 2.3C7 13.4 2.6 9 1.2 2.6z"/></svg>
          555 010 274
        </li>
        <li class="contact__item">
          <svg class="contact__icon" viewBox="0 0 16 16" aria-hidden="true"><path d="M1 3h14v10H1z M2 4.2v.3l6 4.2 6-4.2v-.3z" fill-rule="evenodd"/></svg>
          hello@brightlinegroup.com
        </li>
        <li class="contact__item">
          <svg class="contact__icon" viewBox="0 0 16 16" aria-hidden="true"><circle cx="8" cy="8" r="7"/><path d="M1 8h14M8 1c-3 3.5-3 10.5 0 14M8 1c3 3.5 3 10.5 0 14" stroke="#fff" stroke-width="1" fill="none"/></svg>
          www.brightlinegroup.com
        </li>
      </ul>
    </div>
  </section>

  <section class="card card--back" aria-label="Business card back">
    <div class="back-brand">
      <span class="back-brand__square"></span>
      <span class="back-brand__name">Brightline<br>Electrical Group</span>
    </div>
  </section>
</main>
</body>
</html>
```